I need a business card for my original fine art pieces

I would like a business card design including a logo design for a new business in the art world. I am based in the Hunter Valley NSW Australia. I am a contemporary figurative, encaustic and wildlife artist. I would like to be able to upload my email and mobile number to this as well. This design should be one that I can incorporate into banners and flyers etc. Id like to incorporate one of my own images or partial image into the background or somewhere below. My initials are RJ and I would like these used as a logo type. I would like the use of some colour and it to be bright and catchy. The final design should communicate artwork custom made and commissions available.

Overview: Original Fine Artworks for sale, online, art galleries etc, Custom made to order and by commission.

Target market is world wide audience and corporate world

My figurative work is painted using acrylics in a lot of natural ochre colours that reflect the Australian Outback, on canvas, linen, paper or board: My encaustic work is created in a contemporary abstract style using a blow torch and a made with a medium of 100% pure bees wax, Damar resin, mixed media and coloured pigments, applied to Birch board. My wildlife are created using coloured pencil and mixed media on a variety of paper types or board.

```html
<!DOCTYPE html>
<html lang="en">
<head>
<meta charset="utf-8">
<title>Rhea Jardine – Business Card</title>
<link href="https://fonts.googleapis.com/css2?family=Cinzel:wght@600&family=Open+Sans:wght@400;600&display=swap" rel="stylesheet">
<style>
  :root {
    --bg: #ececec;
    --orange: #f64b0a;
    --paper: #fbfbfa;
    --ink: #3a3a3a;
    --ink-soft: #555555;
    --white: #ffffff;
  }
  * { box-sizing: border-box; margin: 0; padding: 0; }
  html, body {
    width: 1200px; height: 900px; overflow: hidden;
    background: var(--bg);
    font-family: "Open Sans", Arial, sans-serif;
  }
  .sheet {
    width: 1200px; height: 900px;
    display: flex; align-items: center; justify-content: center; gap: 50px;
  }
  .card {
    width: 525px; height: 300px; position: relative;
    box-shadow: 0 4px 14px rgba(0,0,0,0.12);
  }
  .card--back { background: var(--paper); }
  .card--front { background: var(--orange); }

  .contact { position: absolute; left: 40px; top: 34px; color: var(--ink-soft); }
  .contact__name { color: var(--orange); font-weight: 600; font-size: 17px; line-height: 1.1; }
  .contact__role { font-size: 11px; margin-bottom: 10px; }
  .contact__address { font-size: 11px; line-height: 1.45; margin-bottom: 6px; }
  .contact__list { list-style: none; font-size: 11px; line-height: 1.5; }
  .contact__list li { display: flex; align-items: center; gap: 6px; }
  .contact__list svg { width: 9px; height: 9px; flex: none; }

  .brand { position: absolute; display: flex; flex-direction: column; align-items: center; }
  .brand__mark { width: 66px; height: 66px; border-radius: 50%; border: 2.5px solid currentColor; margin-bottom: 6px; }
  .brand__name { font-family: "Cinzel", Georgia, serif; font-weight: 600; font-size: 27px; letter-spacing: 1px; line-height: 1; }
  .brand__tagline { font-size: 11.5px; letter-spacing: 3.2px; text-transform: uppercase; margin-top: 3px; }

  .card--back .brand { right: 38px; bottom: 40px; color: var(--orange); }
  .card--back .brand__tagline { color: var(--ink); }

  .card--front .brand { left: 0; right: 0; top: 48px; color: var(--white); }
  .card--front .brand__mark { width: 80px; height: 80px; }
  .card--front .brand__name { font-size: 31px; }
  .brand__web { font-size: 11px; margin-top: 12px; color: var(--white); }
</style>
</head>
<body>
<main class="sheet">
  <section class="card card--back" aria-label="Business card, contact side">
    <div class="contact">
      <p class="contact__name">Daniel Brooks</p>
      <p class="contact__role">Managing Director</p>
      <p class="contact__address">1234, Address Goes Here<br>Country Name, 123456</p>
      <ul class="contact__list">
        <li><svg viewBox="0 0 10 10"><path d="M2 1h2l1 2-1.2 1a5 5 0 0 0 2.2 2.2L7 5l2 1v2a1 1 0 0 1-1 1A8 8 0 0 1 1 2a1 1 0 0 1 1-1z" fill="var(--orange)"/></svg>123-456-7890</li>
        <li><svg viewBox="0 0 10 10"><rect x="0.5" y="2" width="9" height="6.5" rx="1" fill="var(--orange)"/><path d="M1 2.5l4 3 4-3" stroke="#fff" stroke-width="0.8" fill="none"/></svg>info@youremail.com</li>
        <li><svg viewBox="0 0 10 10"><circle cx="5" cy="5" r="4" fill="none" stroke="var(--orange)" stroke-width="1.2"/><path d="M1 5h8M5 1c-2 2.5-2 5.5 0 8M5 1c2 2.5 2 5.5 0 8" stroke="var(--orange)" stroke-width="0.8" fill="none"/></svg>www.yourweb.com</li>
      </ul>
    </div>
    <div class="brand">
      <span class="brand__mark"></span>
      <p class="brand__name">RHEA JARDINE</p>
      <p class="brand__tagline">Original Fine Artworks</p>
    </div>
  </section>

  <section class="card card--front" aria-label="Business card, logo side">
    <div class="brand">
      <span class="brand__mark"></span>
      <p class="brand__name">RHEA JARDINE</p>
      <p class="brand__tagline">Original Fine Artworks</p>
      <p class="brand__web">www.websitename.com</p>
    </div>
  </section>
</main>
</body>
</html>
```